Business card for Luxury Portable Restroom Trailer company

We are a Luxury Portable Restroom Trailer Company Called FALCRIDGE HIRES. Based in Orange County California. We provide portable restroom trailers for events, such as, Weddings, Concerts, Charity events, Sporting events, Tournaments, Corporate events, ect. We rent and Sell the Luxury restrooms. Our colors are white, grey, and Orange. As you will see in the logo we uploaded.
There are 2 people in the company so the names and titles will change for the 3 people but card will remain the same. Here is the information for each Person: Dwight Penner CFO 555 318-0476
next Person: Leon Marchetti VP 555 318-0476
Next Person: Owen Marchetti CEO 555 318-0476
Information to include on the card: Luxury Restroom Trailers Rental and Sales. Weddings, Concerts, Charity, Sporting and Corp. Events.

```html
<!DOCTYPE html>
<html lang="en">
<head>
<meta charset="utf-8">
<title>Falcridge Hires — Business Card</title>
<link rel="stylesheet" href="https://fonts.googleapis.com/css2?family=Open+Sans:wght@400;600;700&display=swap">
<style>
  :root {
    --page-bg: #2b2b2f;
    --card-bg: #1f1e23;
    --card-bg-warm: #2a2426;
    --orange: #f26a21;
    --grey: #8a8a8e;
    --white: #f4f4f4;
    --emboss: #141317;
    --emboss-edge: #2d2c31;
  }
  * { box-sizing: border-box; margin: 0; padding: 0; }
  html, body { width: 1200px; height: 780px; overflow: hidden; }
  body {
    background: var(--page-bg);
    font-family: "Open Sans", Arial, sans-serif;
    position: relative;
  }
  .card {
    position: absolute;
    top: 230px;
    width: 540px;
    height: 310px;
    border-radius: 22px;
    background: var(--card-bg);
    box-shadow: 0 6px 0 var(--orange), 0 18px 30px rgba(0,0,0,.45);
    overflow: hidden;
  }
  .card--front { left: 40px; background: radial-gradient(ellipse at 55% 45%, var(--card-bg-warm) 0%, var(--card-bg) 70%); }
  .card--back { left: 620px; }

  /* Front */
  .brand-front {
    position: absolute;
    left: 0; right: 0; top: 50%;
    transform: translateY(-50%);
    text-align: center;
    font-weight: 700;
    font-size: 44px;
    letter-spacing: 3px;
    color: var(--orange);
  }

  /* Back */
  .contact {
    position: absolute;
    top: 26px; right: 34px;
    text-align: right;
  }
  .contact__name {
    font-weight: 700;
    font-size: 30px;
    line-height: 1.05;
    color: var(--orange);
  }
  .contact__title {
    font-size: 14px;
    color: var(--grey);
    letter-spacing: 1px;
  }
  .contact__phone {
    margin-top: 2px;
    font-size: 16px;
    color: var(--grey);
    display: flex;
    align-items: center;
    justify-content: flex-end;
    gap: 8px;
  }
  .contact__phone svg { width: 18px; height: 18px; }
  .accent-bar {
    position: absolute;
    top: 0; right: 0;
    width: 14px; height: 64px;
    background: var(--orange);
  }
  .services {
    position: absolute;
    top: 138px; right: 34px;
    list-style: none;
    text-align: right;
    font-size: 15px;
    line-height: 19px;
    color: var(--white);
  }
  .services li { display: flex; align-items: center; justify-content: flex-end; gap: 8px; }
  .services li::after {
    content: "";
    width: 9px; height: 9px;
    border-radius: 50%;
    border: 2px solid var(--orange);
  }
  .tagline {
    position: absolute;
    right: 34px; bottom: 22px;
    font-size: 17px;
    color: var(--white);
  }
  .brand-emboss {
    position: absolute;
    left: 26px; top: 120px;
    transform: rotate(180deg);
    font-weight: 700;
    font-size: 26px;
    letter-spacing: 2px;
    color: var(--emboss);
    text-shadow: 1px 1px 0 var(--emboss-edge);
  }
</style>
</head>
<body>
  <section class="card card--front" aria-label="Card front">
    <div class="brand-front">FALCRIDGE HIRES</div>
  </section>

  <section class="card card--back" aria-label="Card back">
    <div class="accent-bar"></div>
    <div class="contact">
      <div class="contact__name">Dwight Penner</div>
      <div class="contact__title">CFO</div>
      <div class="contact__phone">
        <span>555 318-0476</span>
        <svg viewBox="0 0 18 18" aria-hidden="true">
          <circle cx="9" cy="9" r="9" fill="#f26a21"/>
          <path d="M6.2 4.6l1.4 1.9-.8 1c.5 1.1 1.3 1.9 2.4 2.4l1-.8 1.9 1.4-.8 1.6c-3.3-.4-5.9-3-6.3-6.3z" fill="#f4f4f4"/>
        </svg>
      </div>
    </div>
    <ul class="services">
      <li>Events</li>
      <li>Charity</li>
      <li>Concerts</li>
      <li>Weddings</li>
      <li>Sporting and Corp</li>
    </ul>
    <div class="tagline">Luxury Restroom Trailers Rental and Sales</div>
    <div class="brand-emboss">FALCRIDGE HIRES</div>
  </section>
</body>
</html>
```